Tall Fern Roofing Business Card

Need a business card with the logo that was designed here

Contact Information for Business Card

Name, Title, Phone, Email, Website, Company name

```html
<!DOCTYPE html>
<html lang="en">
<head>
<meta charset="utf-8">
<title>Tall Fern Roofing – Business Card</title>
<link rel="stylesheet" href="https://fonts.googleapis.com/css2?family=Open+Sans:wght@400;600;700&display=swap">
<style>
  :root {
    --brand-blue: #1f74bd;
    --brand-grey: #8e9196;
    --ink: #2b2b2b;
    --paper: #ffffff;
    --backdrop: #d9d9d6;
  }
  * { box-sizing: border-box; margin: 0; padding: 0; }
  html, body { width: 1200px; height: 801px; overflow: hidden; }
  body {
    background: var(--backdrop);
    font-family: "Open Sans", Arial, sans-serif;
    display: flex;
    align-items: center;
    justify-content: center;
    gap: 50px;
  }
  .card {
    position: relative;
    width: 525px;
    height: 300px;
    background: var(--paper);
    box-shadow: 0 10px 30px rgba(0,0,0,0.18);
    overflow: hidden;
  }
  .card__swoosh { position: absolute; inset: 0; }

  /* Front */
  .wordmark {
    color: var(--brand-blue);
    font-weight: 700;
    display: flex;
    align-items: center;
    gap: 10px;
  }
  .wordmark__square {
    width: 14px; height: 14px;
    background: var(--brand-grey);
    flex: none;
  }
  .wordmark__text { line-height: 1.05; }
  .card--front .wordmark {
    position: absolute;
    left: 80px; top: 112px;
    font-size: 26px;
  }
  .card--front .wordmark__roofing { font-size: 17px; letter-spacing: 5px; }
  .divider {
    position: absolute;
    left: 268px; top: 70px;
    width: 1.5px; height: 165px;
    background: var(--brand-blue);
  }
  .contact {
    position: absolute;
    left: 286px; top: 62px;
    color: var(--ink);
    font-size: 12.5px;
    line-height: 1.35;
  }
  .contact__name {
    color: var(--brand-blue);
    font-weight: 700;
    font-size: 20px;
    letter-spacing: 0.5px;
    line-height: 1.1;
  }
  .contact__title { font-size: 11.5px; margin-bottom: 14px; }
  .contact__address { margin-bottom: 14px; }
  .contact__line { display: flex; align-items: center; gap: 6px; }
  .contact__icon { width: 11px; height: 11px; flex: none; }

  /* Back */
  .card--back {
    display: flex;
    align-items: center;
    justify-content: center;
  }
  .card--back .wordmark { font-size: 46px; gap: 16px; }
  .card--back .wordmark__square { width: 22px; height: 22px; }
  .card--back .wordmark__roofing { font-size: 28px; letter-spacing: 10px; }
</style>
</head>
<body>

  <section class="card card--front" aria-label="Business card front">
    <svg class="card__swoosh" viewBox="0 0 525 300" aria-hidden="true">
      <path d="M440,0 H525 V125 C505,72 478,32 440,0Z" fill="var(--brand-blue)"/>
      <path d="M420,0 C462,36 492,82 508,142" fill="none" stroke="var(--brand-grey)" stroke-width="4"/>
      <path d="M85,300 H0 V175 C20,228 47,268 85,300Z" fill="var(--brand-blue)"/>
      <path d="M105,300 C63,264 33,218 17,158" fill="none" stroke="var(--brand-grey)" stroke-width="4"/>
    </svg>

    <div class="wordmark">
      <span class="wordmark__square"></span>
      <span class="wordmark__text">Tall Fern<br><span class="wordmark__roofing">ROOFING</span></span>
    </div>

    <div class="divider"></div>

    <div class="contact">
      <p class="contact__name">DANA WHITLOCK</p>
      <p class="contact__title">Managing Director</p>
      <p class="contact__address">Your address, City<br>State, Zip 1234</p>
      <p class="contact__line">
        <svg class="contact__icon" viewBox="0 0 12 12" aria-hidden="true"><path d="M2.5,1 L4.5,1 L5.3,3.6 L4,4.6 C4.6,6 5.9,7.4 7.4,8 L8.4,6.7 L11,7.5 L11,9.5 C11,10.3 10.3,11 9.5,11 C5,11 1,7 1,2.5 C1,1.7 1.7,1 2.5,1Z" fill="var(--brand-blue)"/></svg>
        123 456 789
      </p>
      <p class="contact__line">
        <svg class="contact__icon" viewBox="0 0 12 12" aria-hidden="true"><rect x="0.5" y="2.5" width="11" height="7.5" fill="var(--brand-blue)"/><path d="M0.5,2.5 L6,7 L11.5,2.5" fill="none" stroke="#fff" stroke-width="1"/></svg>
        info@yourgmail.com
      </p>
      <p class="contact__line">
        <svg class="contact__icon" viewBox="0 0 12 12" aria-hidden="true"><circle cx="6" cy="6" r="5.5" fill="var(--brand-blue)"/><path d="M0.5,6 H11.5 M6,0.5 C3.5,3 3.5,9 6,11.5 M6,0.5 C8.5,3 8.5,9 6,11.5" fill="none" stroke="#fff" stroke-width="0.8"/></svg>
        www.yourwebsite.com
      </p>
    </div>
  </section>

  <section class="card card--back" aria-label="Business card back">
    <div class="wordmark">
      <span class="wordmark__square"></span>
      <span class="wordmark__text">Tall Fern<br><span class="wordmark__roofing">ROOFING</span></span>
    </div>
  </section>

</body>
</html>
```